KVOR Individual and Corporate Development Business Card Design

KVOR needs a business card design that is aligned with it's values and targetted markets. Coherent Lattice of Adaptive Reasoning Method's self diagnosis model and tools, which can be used for personal improvement and team/business performance enhancement, is based on the learnings of over 20 years of medical practitioning. KVOR supercharges personal effectiveness and awareness to also increase team and business performance.

The targetted markets are high performance individuals and teams who aspire seek to enhance their capabilities and achieve their absolute best potential.

Look and feel for the business card design we are looking for is high technology, premium, fresh, new and medical.

Target Market(s)

Industry/Entity Type

Business Consultant

Contact Information for Business Card

Logo, Full Name, Title, Phone number, Email, company name, Address,

Font styles to use
Sans Serif

Requirements
Must have
• Tag line: Sharpening Potential for Truly Ambitious Teams
• Please use same colours as the logo.

```html
<!DOCTYPE html>
<html lang="en">
<head>
<meta charset="utf-8">
<title>KVOR Business Card</title>
<link href="https://fonts.googleapis.com/css2?family=Open+Sans:wght@400;600;700&display=swap" rel="stylesheet">
<style>
  :root {
    --backdrop: #3b3431;
    --card: #0d0d0e;
    --cyan: #00adc6;
    --white: #f2f2f2;
    --rule: #3a3d40;
    --ink: #0f1a1e;
  }
  * { margin: 0; padding: 0; box-sizing: border-box; }
  html, body { width: 1200px; height: 900px; overflow: hidden; }
  body {
    background: var(--backdrop);
    font-family: "Open Sans", Arial, sans-serif;
    position: relative;
  }
  .card {
    position: absolute;
    top: 300px;
    width: 525px;
    height: 300px;
    background: var(--card);
    border-radius: 3px;
    box-shadow: 0 12px 30px rgba(0,0,0,0.45);
    overflow: hidden;
  }
  .card--front { left: 50px; }
  .card--back { left: 625px; }

  .brand { position: absolute; display: flex; flex-direction: column; align-items: flex-start; color: var(--cyan); font-weight: 700; }
  .brand__row { display: flex; align-items: center; gap: 12px; }
  .brand__dot { width: 14px; height: 14px; border-radius: 50%; background: var(--cyan); }
  .brand__name { font-size: 62px; line-height: 1; letter-spacing: 2px; }
  .brand__desc { font-size: 11.5px; line-height: 1.25; letter-spacing: 0.6px; text-transform: uppercase; margin-top: 8px; border-top: 1px solid var(--rule); padding-top: 6px; width: 260px; }

  .card--front .brand { left: 235px; top: 52px; }
  .card--back .brand { left: 135px; top: 30px; }

  .person { position: absolute; left: 42px; top: 100px; }
  .person__name { color: var(--cyan); font-weight: 600; font-size: 16px; letter-spacing: 0.5px; text-transform: uppercase; }
  .person__title { color: var(--white); font-size: 13px; margin-top: 2px; }

  .contacts { position: absolute; left: 62px; top: 158px; list-style: none; }
  .contacts li { display: flex; align-items: center; gap: 8px; color: var(--white); font-size: 13px; line-height: 20px; }
  .contacts svg { width: 11px; height: 11px; fill: var(--cyan); }

  .address { position: absolute; left: 80px; top: 226px; color: var(--white); font-size: 13px; font-weight: 600; line-height: 17px; }
  .address__company { color: var(--cyan); font-weight: 700; }

  .tagline-band {
    position: absolute; left: 0; right: 0; top: 175px; height: 85px;
    background: var(--cyan);
    display: flex; align-items: center; justify-content: center; text-align: center;
  }
  .tagline {
    color: var(--ink); font-weight: 700; font-size: 17px; letter-spacing: 2px; line-height: 24px; text-transform: uppercase;
  }
</style>
</head>
<body>

  <section class="card card--front" aria-label="Business card front">
    <div class="brand">
      <div class="brand__row"><span class="brand__dot"></span><span class="brand__name">KVOR</span></div>
      <div class="brand__desc">Coherent Lattice of<br>Adaptive Reasoning Method</div>
    </div>

    <div class="person">
      <p class="person__name">Dorian Vale</p>
      <p class="person__title">Managing Director</p>
    </div>

    <ul class="contacts">
      <li><svg viewBox="0 0 12 12"><path d="M1 3c0-1 1-2 2-2h1l1 2-1 1c.5 1.5 2 3 3.5 3.5l1-1 2 1v1c0 1-1 2-2 2C4.5 10.5 1 7 1 3z"/></svg>777 210 384</li>
      <li><svg viewBox="0 0 12 12"><path d="M0 2h12v8H0z M1 3l5 3.5L11 3" stroke="#0d0d0e" stroke-width="1"/></svg>info@kvor.com</li>
      <li><svg viewBox="0 0 12 12"><circle cx="6" cy="6" r="5.5"/></svg>www.kvor.com</li>
    </ul>

    <div class="address">
      <p class="address__company">KVOR</p>
      <p>Address line one here,</p>
      <p>Address line two here.</p>
    </div>
  </section>

  <section class="card card--back" aria-label="Business card back">
    <div class="brand">
      <div class="brand__row"><span class="brand__dot"></span><span class="brand__name">KVOR</span></div>
      <div class="brand__desc">Coherent Lattice of<br>Adaptive Reasoning Method</div>
    </div>
    <div class="tagline-band">
      <p class="tagline">Sharpening Potential for<br>Truly Ambitious Teams</p>
    </div>
  </section>

</body>
</html>
```